Business Card Design Project - del varosi group

dear Sirs

we need business card design for our group ( DEL Varosi Group ) , i have got the Logo design of our group from pixel harbor in previous , so all need details relating to our group i think available with you, as well as the the chosen logo design

we hope to provide us with business card logo that to be appropaite and satisfactory to us .

thanks

note : logo design of our group is attached .
Updates

Reason: please extend the deadline of my project for additional 15 days because i didn't received appropriate design for our gruop yet . kindly beaware that i have received 77 design till now , supossed to send me 200-250 design at least . thanks

Target Market(s)

contents

name : Kerem EL Nadiri

position : Operation Manager

Industry/Entity Type

Business

Requirements
Must have

• person name

group logo
Nice to have
• logo color matching with back background

```html
<!DOCTYPE html>
<html lang="en">
<head>
<meta charset="utf-8">
<title>DEL Varosi Group – Business Card</title>
<link href="https://fonts.googleapis.com/css2?family=Cinzel:wght@400;600;700&display=swap" rel="stylesheet">
<style>
  :root {
    --page-bg: #d9dcdf;
    --card-dark: #262425;
    --card-light: #e9e7e8;
    --brand-blue: #1d5a9e;
    --ink-dark: #1c1a1b;
    --accent-gold: #d9a53a;
  }
  html, body {
    margin: 0;
    padding: 0;
    width: 1067px;
    height: 1200px;
    overflow: hidden;
    background: var(--page-bg);
    font-family: "Cinzel", Georgia, serif;
  }
  .canvas {
    position: relative;
    width: 1067px;
    height: 1200px;
  }
  .card {
    position: absolute;
    left: 103px;
    width: 860px;
    height: 491px;
    box-shadow: 0 6px 18px rgba(0,0,0,0.25);
    overflow: hidden;
  }
  .card--front { top: 66px; }
  .card--back  { top: 643px; }
  .card__shapes {
    position: absolute;
    inset: 0;
    width: 100%;
    height: 100%;
  }
  .shape-dark  { fill: var(--card-dark); }
  .shape-band  { fill: var(--brand-blue); }
  .shape-light { fill: var(--card-light); }

  /* Front: rotated group name on dark panel */
  .front-brand {
    position: absolute;
    left: 165px;
    top: 245px;
    transform: translate(-50%, -50%) rotate(-90deg);
    display: flex;
    align-items: center;
    gap: 14px;
    white-space: nowrap;
  }
  .brand-mark {
    width: 24px;
    height: 24px;
    background: var(--accent-gold);
    flex: none;
  }
  .brand-name {
    color: var(--brand-blue);
    font-weight: 600;
    letter-spacing: 2px;
    text-transform: uppercase;
  }
  .front-brand .brand-name {
    font-size: 34px;
    letter-spacing: 1px;
  }

  /* Front: contact details */
  .details {
    position: absolute;
    left: 430px;
    top: 38px;
    right: 30px;
  }
  .person-name {
    margin: 0;
    color: var(--brand-blue);
    font-size: 36px;
    font-weight: 700;
    letter-spacing: 1px;
    text-transform: uppercase;
  }
  .person-title {
    margin: 4px 0 0;
    color: var(--ink-dark);
    font-size: 17px;
    font-weight: 700;
  }
  .contact-list {
    list-style: none;
    margin: 52px 0 0;
    padding: 0;
    color: var(--ink-dark);
    font-size: 22px;
    font-weight: 600;
    line-height: 44px;
  }
  .web-list {
    list-style: none;
    margin: 62px 0 0;
    padding: 0;
    color: var(--brand-blue);
    font-size: 21px;
    font-weight: 600;
    line-height: 44px;
    text-transform: uppercase;
  }

  /* Back: centred group name */
  .back-brand {
    position: absolute;
    left: 345px;
    top: 245px;
    transform: translate(-50%, -50%);
    display: flex;
    align-items: center;
    gap: 18px;
    white-space: nowrap;
  }
  .back-brand .brand-name { font-size: 48px; }
</style>
</head>
<body>
<main class="canvas">

  <section class="card card--front" aria-label="Business card front">
    <svg class="card__shapes" viewBox="0 0 860 491" preserveAspectRatio="none" aria-hidden="true">
      <rect class="shape-light" x="0" y="0" width="860" height="491"/>
      <polygon class="shape-band" points="0,0 376,0 346,128 402,491 0,491"/>
      <polygon class="shape-dark" points="0,0 352,0 322,128 378,491 0,491"/>
    </svg>

    <div class="front-brand">
      <span class="brand-mark"></span>
      <span class="brand-name">DEL Varosi Group</span>
    </div>

    <div class="details">
      <h1 class="person-name">Kerem EL Nadiri</h1>
      <p class="person-title">Operation Manager</p>
      <ul class="contact-list">
        <li>Phone: 0123 456 789</li>
        <li>Fax: 0123 456 789</li>
        <li>PO. Box: City Name, Etc.</li>
      </ul>
      <ul class="web-list">
        <li>info yourdomain.com</li>
        <li>www.yourdomain.com</li>
      </ul>
    </div>
  </section>

  <section class="card card--back" aria-label="Business card back">
    <svg class="card__shapes" viewBox="0 0 860 491" preserveAspectRatio="none" aria-hidden="true">
      <rect class="shape-light" x="0" y="0" width="860" height="491"/>
      <polygon class="shape-band" points="0,0 736,0 704,196 718,491 0,491"/>
      <polygon class="shape-dark" points="0,0 712,0 680,196 694,491 0,491"/>
    </svg>

    <div class="back-brand">
      <span class="brand-mark"></span>
      <span class="brand-name">DEL Varosi Group</span>
    </div>
  </section>

</main>
</body>
</html>
```